Thoroughbred Racing Partnership needs web design

Glimmer of Laurel Partners is a management group who buys horses and races them on both the West and East coasts. The premise of the business is for an investment as little as $500, anyone can be a partner and own a percentage of a horse(s). This is a low cost way of getting involved in the exciting sport of Thoroughbred Racing, without shouldering the heavy financial responsibility. Our target market is mostly males 40+ but we want to include all target markets. We are looking for something very clean and professional, we want to give an image of success. Nothing overly "artsy." I have included the logo in which you can incorporate in the site. Also, the logo colors will be the colors of our "silks." The silks are what the jockey wears and will be an important marketing tool for GOL. We would like a very prominent picture of a racehorse somewhere on the homepage, we want to make it clear that is a website for Horseracing partnerships.

On the top of the site, it should say "Glimmer of Laurel" (on the top)
and below that "Thoroughbred Racing Partnerships." (below that)

The main sections, which should be across the top are:

Home
About Us
Ownership
Stable Roster
News
Contact us

Some of these will have drop down menus.

An example of a competitor website that we like is: www.harrowgatefarm.example
An example of a competitor website that we don't like is: www.paddockvue.example
Updates

Project Deadline Extended
Reason: We have a Board of Directors meeting on the 22nd and we will be making a decision on that day. I'm giving an extension so that all designers are able to submit their designs by the 22nd. Thank you!

Target Market(s)

40+ males

Industry/Entity Type

Business

Requirements
Must have
• our logo must be on the site. We would like at least one bold image of a thoroughbred horse in action. The picture is going to tell the story so it needs to be very eye-catching.

Our slogan should also be included on the website, "Experience the thrill of owning a Racehorse."
Should not have
• cartoons, artsy pictures, pictures of Steeplechase horses or "jumpers." This partnership is for racehorses only, there is not jumping involved with the horses.

```html
<!DOCTYPE html>
<html lang="en">
<head>
<meta charset="utf-8">
<title>Glimmer of Laurel – Thoroughbred Racing Partnerships</title>
<link rel="stylesheet" href="https://fonts.googleapis.com/css2?family=Arvo:ital,wght@0,400;0,700;1,700&family=Open+Sans:wght@300;400;600&display=swap">
<style>
:root{
  --gold:#dca11b;
  --gold-text:#e0a82a;
  --ink:#ffffff;
  --muted:#cfcfcf;
  --dim:#9a9a9a;
  --bar:#1c1c1c;
  --page:#2a2a2a;
  --panel-dark:#141414;
  --panel-grey:#3a3a3a;
  --footer:#242424;
  --field:#f4f4f4;
}
*{box-sizing:border-box;margin:0;padding:0}
html,body{width:1200px;height:2347px;overflow:hidden}
body{position:relative;font-family:"Open Sans",Arial,sans-serif;color:var(--ink);
  background:linear-gradient(180deg,#1e1e1e 0,#3a3a3a 300px,#2d2d2d 900px,#333 1100px,#1f1f1f 1500px,#2a2a2a 1980px)}
.abs{position:absolute}
.heading{font-family:"Arvo",Georgia,serif;font-weight:700}

/* top bar */
.topbar{left:0;top:0;width:1200px;height:40px;background:var(--bar);font-size:12px;color:var(--dim)}
.topbar .contact{left:16px;top:11px}
.social{display:flex;gap:9px}
.social span{width:15px;height:15px;background:#9a9a9a;border-radius:2px;display:block}
.topbar .social{right:18px;top:12px}

/* header */
.header{left:0;top:40px;width:1200px;height:115px;background:rgba(20,20,20,.55)}
.brand{left:45px;top:30px;display:flex;align-items:center;gap:10px;font-weight:600;font-size:26px;line-height:1}
.brand i{width:16px;height:16px;background:#fff;border-radius:50%;display:block}
.site-title{right:34px;top:26px;text-align:right}
.site-title h1{font-family:"Arvo",serif;font-style:italic;font-weight:700;font-size:39px;letter-spacing:1px;line-height:1.1}
.site-title p{font-size:24px;color:var(--gold-text);font-weight:400;line-height:1.2}

/* nav */
.nav{left:17px;top:155px;display:flex;height:52px;font-size:16px;font-weight:600;letter-spacing:.5px}
.nav a{color:#fff;text-decoration:none;padding:0 19px;line-height:52px}
.nav a.active{background:var(--gold);padding:0 25px}

/* hero */
.hero-media{left:144px;top:208px;width:910px;height:355px;
  background:
    radial-gradient(ellipse 38% 60% at 72% 45%,rgba(255,255,255,.95) 0,rgba(255,255,255,0) 70%),
    radial-gradient(ellipse 30% 45% at 85% 70%,rgba(40,40,40,.55) 0,rgba(40,40,40,0) 70%),
    radial-gradient(ellipse 40% 55% at 45% 60%,rgba(230,230,225,.9) 0,rgba(230,230,225,0) 70%),
    linear-gradient(90deg,#e9e4bd 0,#f3f0da 35%,#d9d6c4 60%,#e6e0b5 100%)}
.slide-arrow{top:367px;width:34px;height:34px;border-radius:50%;background:#111;display:flex;align-items:center;justify-content:center}
.hero-title{left:0;width:1200px;top:585px;text-align:center;font-size:36px;letter-spacing:2px}
.hero-sub{left:0;width:1200px;top:648px;text-align:center;font-size:31px;font-weight:300;color:#d8d8d8;line-height:40px;letter-spacing:1px}
.hero-sub em{font-style:normal;color:var(--gold-text)}
.cta{left:449px;top:748px;width:288px;height:50px;background:var(--gold);display:flex;align-items:center;font-size:30px;font-weight:300;letter-spacing:1px}
.cta svg{margin:0 32px 0 22px}

/* feature boxes */
.feature{top:867px;height:191px;padding:20px 9px 0 9px}
.feature.dark{background:var(--panel-dark);border:1px solid #444}
.feature.grey{background:var(--panel-grey)}
.feature h3{display:flex;align-items:center;gap:12px;font-size:28px;margin:0 0 10px 6px}
.feature p{font-size:12.5px;line-height:19px;color:#e6e6e6;padding-left:8px}
.btn-dark{position:absolute;left:9px;top:138px;height:38px;background:#000;border:1px solid #555;display:flex;align-items:center;gap:12px;padding:0 16px 0 10px;font-size:14px}

/* about */
.video{left:46px;top:1089px;width:416px;height:202px;background:#111}
.video-frame{left:0;top:0;width:416px;height:180px;
  background:
    radial-gradient(ellipse 22% 40% at 20% 55%,rgba(120,60,30,.85) 0,rgba(120,60,30,0) 70%),
    radial-gradient(ellipse 18% 38% at 36% 45%,rgba(90,45,25,.8) 0,rgba(90,45,25,0) 70%),
    radial-gradient(ellipse 12% 28% at 80% 55%,rgba(110,60,30,.75) 0,rgba(110,60,30,0) 70%),
    linear-gradient(180deg,#a8b48a 0,#8ea262 35%,#6f9a34 60%,#5a8a28 100%)}
.video-controls{left:0;top:180px;width:416px;height:22px;background:#1a1a1a;font-size:9px;color:#ccc}
.about-title{left:617px;top:1128px;font-size:28px}
.about-text{left:617px;top:1172px;width:562px;font-size:13px;line-height:16px;color:#e6e6e6}
.btn-gold{background:var(--gold);display:flex;align-items:center;color:#fff}
.about-btn{left:981px;top:1235px;width:172px;height:38px;font-size:18px;gap:14px;padding-left:12px}

/* horses */
.horses-title{left:18px;top:1360px;font-size:29px;font-weight:400;color:var(--gold-text)}
.horses-text{left:18px;top:1402px;font-size:13px;color:#f0f0f0}
.carousel-nav{left:17px;top:1437px;width:59px;height:21px;background:var(--gold);display:flex;justify-content:space-around;align-items:center}
.horse{top:1458px;height:202px}

/* testimonial */
.testimonial{left:17px;top:1726px;width:1160px;height:195px;background:rgba(25,25,25,.85);border-top:2px solid #555}
.testimonial h2{position:absolute;left:18px;top:22px;font-size:31px;letter-spacing:1px}
.testimonial .who{position:absolute;left:20px;top:68px;font-size:30px;font-weight:300;color:var(--gold-text)}
.testimonial .who small{font-size:20px;color:#fff;font-weight:400}
.testimonial p{position:absolute;left:20px;top:106px;width:1010px;font-size:15px;line-height:27px;color:#cfcfcf}
.testimonial .btn-gold{position:absolute;left:892px;top:146px;width:244px;height:38px;font-size:19px;gap:6px;padding-left:8px}

/* footer */
.footer{left:0;top:1978px;width:1200px;height:369px;background:var(--footer)}
.footer h4{position:absolute;top:36px;font-family:"Arvo",serif;font-weight:400;font-size:19px;color:#e6e6e6;letter-spacing:.5px}
.tweet{position:absolute;left:17px;font-size:12px;line-height:20px;color:#ddd}
.tweet a{color:var(--gold-text);text-decoration:none}
.tweet time{color:#888;margin-left:6px}
.tweet .t{display:flex;gap:6px;align-items:center}
.album{left:314px;top:88px;display:grid;grid-template-columns:repeat(4,46px);grid-gap:14px 11px}
.album span{height:33px;border:1px solid #777;display:block}
.touch{left:617px;top:92px;font-size:12px;line-height:20px;color:#ddd}
.touch .mail{color:var(--gold-text);display:flex;align-items:center;gap:6px}
.touch .phone{display:flex;align-items:center;gap:12px;font-size:29px;color:var(--gold-text);margin-top:12px}
.touch .social{margin-top:18px}
.field{background:var(--field);border:1px solid #ccc;color:#888;font-size:12px;display:flex;justify-content:center;align-items:center}
.submit{left:1071px;top:240px;width:106px;height:36px;background:#000;display:flex;align-items:center;gap:14px;padding-left:12px;font-size:15px}
.bottombar{left:0;top:2297px;width:1200px;height:50px;background:#222;border-top:2px solid #3a3a3a;font-size:12px;color:#bbb}
.bottombar .copy{position:absolute;left:19px;top:16px}
.bottombar .links{position:absolute;right:62px;top:16px;display:flex;gap:8px;color:#eee}
.totop{right:12px;top:0;width:34px;height:34px;background:#555;display:flex;align-items:center;justify-content:center}
</style>
</head>
<body>

<div class="abs topbar">
  <span class="abs contact">&#9906; 1800 Furlong Row , UK &nbsp;&#9743; 1.555.010.2200</span>
  <div class="abs social"><span></span><span></span><span></span><span></span></div>
</div>

<header class="abs header">
  <div class="abs brand"><i></i>GOL Partners</div>
  <div class="abs site-title">
    <h1>Glimmer of Laurel</h1>
    <p>Thoroughbred Racing Partnerships</p>
  </div>
</header>

<nav class="abs nav">
  <a class="active" href="#">Home</a><a href="#">About Us</a><a href="#">Ownership</a><a href="#">Stable Roster</a><a href="#">News</a><a href="#">Contact</a>
</nav>

<div class="abs hero-media" role="img" aria-label="Bold black and white photo of a white thoroughbred racehorse head wearing a dark bridle"></div>
<div class="abs slide-arrow" style="left:147px"><svg width="12" height="12" viewBox="0 0 12 12"><path d="M8 1 3 6l5 5" stroke="#fff" stroke-width="2" fill="none"/></svg></div>
<div class="abs slide-arrow" style="left:1014px"><svg width="12" height="12" viewBox="0 0 12 12"><path d="M4 1l5 5-5 5" stroke="#fff" stroke-width="2" fill="none"/></svg></div>

<h2 class="abs heading hero-title">Experience the thrill of owning a Racehorse</h2>
<p class="abs hero-sub">Be a part of the thrilling event with just an<br>investment of as little as <em>$500</em></p>
<a class="abs cta"><svg width="26" height="18" viewBox="0 0 26 18"><path d="M2 9h20M14 2l8 7-8 7" stroke="#fff" stroke-width="3" fill="none"/><path d="M2 4v10" stroke="#fff" stroke-width="3"/></svg>Know How</a>

<section class="abs feature dark" style="left:8px;width:292px">
  <h3 class="heading"><svg width="26" height="28" viewBox="0 0 26 28"><circle cx="13" cy="8" r="7" fill="#dca11b"/><path d="M0 28c0-9 6-12 13-12s13 3 13 12z" fill="#dca11b"/></svg>Ownership</h3>
  <p>Lorem ipsum dolor sit amet, consectetur adipisicing elit, sed do eiusmod tempor incididunt ut labore</p>
  <span class="btn-dark"><svg width="14" height="12" viewBox="0 0 14 12"><path d="M1 6h11M7 1l5 5-5 5" stroke="#fff" stroke-width="2" fill="none"/></svg>Read More</span>
</section>
<section class="abs feature grey" style="left:301px;width:298px">
  <h3 class="heading"><svg width="28" height="26" viewBox="0 0 28 26"><path d="M27 1 1 12l9 3 2 10 4-7 6 4z" fill="#dca11b"/></svg>Stable Roster</h3>
  <p>Lorem ipsum dolor sit amet, consectetur adipisicing elit, sed do eiusmod tempor incididunt ut labore</p>
  <span class="btn-dark"><svg width="14" height="12" viewBox="0 0 14 12"><path d="M1 6h11M7 1l5 5-5 5" stroke="#fff" stroke-width="2" fill="none"/></svg>Read More</span>
</section>
<section class="abs feature grey" style="left:601px;width:293px">
  <h3 class="heading"><svg width="24" height="30" viewBox="0 0 24 30"><path d="M0 0h16l8 8v22H0z" fill="#dca11b"/><path d="M5 12h14M5 17h14M5 22h10" stroke="#3a3a3a" stroke-width="2"/></svg>News</h3>
  <p>Lorem ipsum dolor sit amet, consectetur adipisicing elit, sed do eiusmod tempor incididunt ut labore</p>
  <span class="btn-dark"><svg width="14" height="12" viewBox="0 0 14 12"><path d="M1 6h11M7 1l5 5-5 5" stroke="#fff" stroke-width="2" fill="none"/></svg>Read More</span>
</section>
<section class="abs feature dark" style="left:897px;width:293px">
  <h3 class="heading"><svg width="28" height="28" viewBox="0 0 28 28"><rect x="2" y="4" width="24" height="22" fill="none" stroke="#dca11b" stroke-width="3"/><path d="M2 10h24M8 1v6M20 1v6" stroke="#dca11b" stroke-width="3"/></svg>Events</h3>
  <p>Lorem ipsum dolor sit amet, consectetur adipisicing elit, sed do eiusmod tempor incididunt ut labore</p>
  <span class="btn-dark"><svg width="14" height="12" viewBox="0 0 14 12"><path d="M1 6h11M7 1l5 5-5 5" stroke="#fff" stroke-width="2" fill="none"/></svg>Read More</span>
</section>

<div class="abs video">
  <div class="abs video-frame" role="img" aria-label="Video still of jockeys racing thoroughbred horses at full gallop on a grass track"></div>
  <svg class="abs" style="left:173px;top:56px" width="68" height="50" viewBox="0 0 68 50"><rect width="68" height="50" rx="8" fill="#1a1a1a" opacity=".85"/><path d="M26 13v24l20-12z" fill="#fff"/></svg>
  <div class="abs video-controls">
    <div class="abs" style="left:0;top:0;width:416px;height:3px;background:#555"></div>
    <div class="abs" style="left:0;top:0;width:36px;height:3px;background:#c00"></div>
    <span class="abs" style="left:8px;top:5px">&#9654;&nbsp;&nbsp;&#9834;&nbsp;&nbsp;0:02 / 4:17</span>
    <span class="abs" style="right:10px;top:5px">&#9679; &#9881; &#9634;</span>
  </div>
</div>
<h2 class="abs heading about-title">About Us</h2>
<p class="abs about-text">Lorem ipsum dolor sit amet, consectetur adipisicing elit, sed do eiusmod tempor incididunt ut labore et dolore magna aliqua. Ut enim ad minim veniam, quis nostrud exercitation ullamco laboris nisi ut aliquip ex ea commodo consequat.</p>
<a class="abs btn-gold about-btn"><svg width="14" height="12" viewBox="0 0 14 12"><path d="M1 6h11M7 1l5 5-5 5" stroke="#fff" stroke-width="2" fill="none"/></svg>Read More</a>

<h2 class="abs heading horses-title">The Horses of Choice</h2>
<p class="abs horses-text">Lorem ipsum dolor sit amet, consectetur adipisicing elit, sed do eiusmod tempor incididunt ut</p>
<div class="abs carousel-nav">
  <svg width="14" height="10" viewBox="0 0 14 10"><path d="M13 5H2M6 1 2 5l4 4" stroke="#fff" stroke-width="1.6" fill="none"/></svg>
  <svg width="14" height="10" viewBox="0 0 14 10"><path d="M1 5h11M8 1l4 4-4 4" stroke="#fff" stroke-width="1.6" fill="none"/></svg>
</div>
<div class="abs horse" style="left:18px;width:285px;background:radial-gradient(ellipse 55% 60% at 45% 55%,#b5622a 0,#8a4a20 45%,rgba(90,42,18,0) 80%),linear-gradient(120deg,#f2efe8 0,#e8d8c4 35%,#5a2a12 100%)" role="img" aria-label="Photo of a chestnut racehorse head in a bridle"></div>
<div class="abs horse" style="left:313px;width:284px;background:radial-gradient(ellipse 45% 55% at 55% 60%,#3a2a22 0,rgba(58,42,34,0) 75%),radial-gradient(ellipse 20% 25% at 35% 70%,rgba(220,220,220,.7) 0,rgba(220,220,220,0) 70%),linear-gradient(160deg,#a9b2b8 0,#6a6660 50%,#2a211b 100%)" role="img" aria-label="Photo of a dark bay racehorse with a saddle cloth"></div>
<div class="abs horse" style="left:604px;width:285px;background:radial-gradient(ellipse 50% 55% at 45% 55%,#c06a62 0,#9a4a44 40%,rgba(60,40,34,0) 80%),linear-gradient(120deg,#2a1e18 0,#5a3a30 45%,#e3c7b8 100%)" role="img" aria-label="Photo of a racehorse wearing a red racing hood"></div>
<div class="abs horse" style="left:894px;width:283px;background:radial-gradient(ellipse 45% 60% at 40% 50%,#f3ead4 0,#d8c08e 45%,rgba(90,60,30,0) 85%),linear-gradient(120deg,#2e2012 0,#7a5a30 40%,#e8d8b0 100%)" role="img" aria-label="Photo of a pale horse with a flowing mane"></div>

<section class="abs testimonial">
  <h2 class="heading">See what our &nbsp;Partners are saying</h2>
  <div class="who">Sam Carter, <small>CEO. Marlow Holdings Inc.</small></div>
  <p>Lorem ipsum dolor sit amet, consectetur adipisicing elit, sed do eiusmod tempor incididunt ut labore et dolore magna aliqua. Ut enim ad minim veniam, quis nostrud exercitation ullamco laboris nisi ut aliquip ex ea commodo consequat.</p>
  <a class="btn-gold"><svg width="30" height="22" viewBox="0 0 30 22"><path d="M2 11h24M16 2l10 9-10 9" stroke="#fff" stroke-width="3" fill="none"/></svg>View All Testimonials</a>
</section>

<footer class="abs footer">
  <h4 style="left:17px">Latest Tweets</h4>
  <h4 style="left:314px">Latest Album</h4>
  <h4 style="left:617px">Get In Touch</h4>
  <h4 style="left:907px">Quick Contact</h4>

  <div class="tweet" style="top:88px"><div class="t"><svg width="14" height="12" viewBox="0 0 14 12"><path d="M1 10c5 2 11-1 11-7l2-2-2 1-1-1C9 0 7 1 7 4 5 4 3 3 1 1c0 2 1 4 2 4H2c0 2 2 3 3 3-1 1-3 2-4 2z" fill="#ccc"/></svg>Lorem ipsum dolor sit ---- I am Owen</div><a>http://vid.example/Rk4tQp_2?a</a><time>2013/10/24</time></div>
  <div class="tweet" style="top:149px"><div class="t"><svg width="14" height="12" viewBox="0 0 14 12"><path d="M1 10c5 2 11-1 11-7l2-2-2 1-1-1C9 0 7 1 7 4 5 4 3 3 1 1c0 2 1 4 2 4H2c0 2 2 3 3 3-1 1-3 2-4 2z" fill="#ccc"/></svg>Lorem ipsum dolor sit ---- I am Owen</div><a>http://vid.example/Rk4tQp_2?a</a><time>2013/10/24</time></div>
  <div class="tweet" style="top:209px"><div class="t"><svg width="14" height="12" viewBox="0 0 14 12"><path d="M1 10c5 2 11-1 11-7l2-2-2 1-1-1C9 0 7 1 7 4 5 4 3 3 1 1c0 2 1 4 2 4H2c0 2 2 3 3 3-1 1-3 2-4 2z" fill="#ccc"/></svg>Lorem ipsum dolor sit ---- I am Owen</div><a>http://vid.example/Rk4tQp_2?a</a><time>2013/10/24</time></div>
  <div class="tweet" style="top:270px"><div class="t"><svg width="14" height="12" viewBox="0 0 14 12"><path d="M1 10c5 2 11-1 11-7l2-2-2 1-1-1C9 0 7 1 7 4 5 4 3 3 1 1c0 2 1 4 2 4H2c0 2 2 3 3 3-1 1-3 2-4 2z" fill="#ccc"/></svg>Lorem ipsum dolor sit ---- I am Owen</div><a>http://vid.example/Rk4tQp_2?a</a><time>2013/10/24</time></div>

  <div class="abs album" role="img" aria-label="Grid of twelve small horse racing photos">
    <span style="background:linear-gradient(135deg,#9a9a9a,#4a4a4a)"></span><span style="background:linear-gradient(135deg,#d0d0d0,#3a3a3a)"></span><span style="background:linear-gradient(135deg,#a04a34,#4a1a12)"></span><span style="background:linear-gradient(135deg,#d8cab8,#6a5a48)"></span>
    <span style="background:linear-gradient(135deg,#8a6a4a,#2a1e14)"></span><span style="background:linear-gradient(135deg,#8a8a8a,#2a2a2a)"></span><span style="background:linear-gradient(135deg,#d8a67e,#7a4a2a)"></span><span style="background:linear-gradient(135deg,#c0b4a0,#5a5040)"></span>
    <span style="background:linear-gradient(135deg,#b0b0b0,#4a4a4a)"></span><span style="background:linear-gradient(135deg,#9a8a70,#3a3020)"></span><span style="background:linear-gradient(135deg,#e0b890,#7a5030)"></span><span style="background:linear-gradient(135deg,#b0a498,#4a4038)"></span>
  </div>

  <div class="abs touch">
    47 Laurel Gate Lane<br>Brookfield, MO 65550
    <div class="mail"><svg width="11" height="8" viewBox="0 0 11 8"><rect width="11" height="8" fill="#dca11b"/><path d="M0 0l5.5 4L11 0" stroke="#242424" fill="none"/></svg>info@glimmeroflaurelpartners</div>
    <div class="phone"><svg width="26" height="46" viewBox="0 0 26 46"><rect x="2" y="2" width="22" height="42" rx="4" fill="none" stroke="#888" stroke-width="3"/><rect x="6" y="8" width="14" height="26" fill="#888"/><circle cx="13" cy="39" r="2" fill="#888"/></svg>155501022000</div>
    <div class="social"><span></span><span></span><span></span><span></span></div>
  </div>

  <div class="abs field" style="left:909px;top:94px;width:121px;height:26px">Name</div>
  <div class="abs field" style="left:1056px;top:94px;width:121px;height:26px">Email</div>
  <div class="abs field" style="left:909px;top:130px;width:268px;height:101px;justify-content:flex-start;align-items:flex-start;padding:6px">Message</div>
  <a class="abs submit"><svg width="14" height="12" viewBox="0 0 14 12"><path d="M1 6h11M7 1l5 5-5 5" stroke="#fff" stroke-width="2" fill="none"/></svg>Submit</a>
</footer>

<div class="abs bottombar">
  <span class="copy">@Copyright message</span>
  <div class="links"><span>Home</span><span>About Us</span><span>Ownership</span><span>Stable Roster</span><span>News</span><span>Contact</span></div>
  <div class="abs totop"><svg width="14" height="10" viewBox="0 0 14 10"><path d="M1 9l6-7 6 7" stroke="#ddd" stroke-width="2" fill="none"/></svg></div>
</div>

</body>
</html>
```